Upscale business cards needed for Board of Directors

We need professional business cards created for members of our family business Board of Directors. We would like these relatively simple and straightforward, but also with a unique element to set them apart. Probably stick with neutral and simple colors - white, grey etc. We need space for the traditional elements, including name, title, address, email/phone number. And we will be creating several from this template so it needs to be template that is easy to switch information in and out of.
Business
See description

```html
<!DOCTYPE html>
<html lang="en">
<head>
<meta charset="utf-8">
<title>Harborline Holdings Business Cards</title>
<link href="https://fonts.googleapis.com/css2?family=Lato:wght@400;700;900&display=swap" rel="stylesheet">
<style>
  :root {
    --page: #e6e5e2;
    --ink: #0a0a0a;
    --paper: #ffffff;
    --gold: #b19e74;
    --gold-text: #a8916a;
    --shadow: rgba(0, 0, 0, 0.18);
  }
  * { box-sizing: border-box; margin: 0; padding: 0; }
  html, body {
    width: 1200px;
    height: 900px;
    overflow: hidden;
    background: var(--page);
    font-family: "Lato", sans-serif;
  }
  .canvas {
    position: relative;
    width: 1200px;
    height: 900px;
  }
  .card {
    position: absolute;
    left: 300px;
    width: 600px;
    height: 343px;
    box-shadow: 0 8px 24px var(--shadow);
    overflow: hidden;
  }
  /* Front */
  .card-front {
    top: 77px;
    background: var(--ink);
    color: var(--paper);
    text-align: center;
  }
  .brand-name {
    position: absolute;
    top: 92px;
    left: 0;
    right: 0;
    font-weight: 900;
    text-transform: uppercase;
    line-height: 1;
  }
  .brand-name .line-main {
    display: block;
    font-size: 46px;
    letter-spacing: 1px;
  }
  .brand-name .line-sub {
    display: block;
    margin-top: 10px;
    font-size: 22px;
    letter-spacing: 14px;
    padding-left: 14px;
  }
  .front-web {
    position: absolute;
    top: 238px;
    left: 0;
    right: 0;
    font-size: 15px;
    letter-spacing: 2px;
  }
  /* Back */
  .card-back {
    top: 480px;
    background: var(--paper);
  }
  .name-block {
    position: absolute;
    left: 0;
    top: 66px;
    width: 262px;
    height: 108px;
    background: var(--ink);
    padding: 26px 0 0 38px;
  }
  .person-name {
    color: var(--paper);
    font-size: 21px;
    font-weight: 400;
  }
  .person-title {
    color: var(--gold-text);
    font-size: 14px;
    margin-top: 2px;
  }
  .contact-panel {
    position: absolute;
    left: 270px;
    right: 0;
    top: 66px;
    height: 216px;
    background: var(--gold);
  }
  .panel-rule {
    position: absolute;
    left: 20px;
    top: 18px;
    width: 2px;
    height: 150px;
    background: var(--paper);
  }
  .contact-list {
    position: absolute;
    left: 42px;
    top: 18px;
    color: var(--paper);
    font-size: 15px;
    line-height: 19px;
    list-style: none;
  }
  .address { margin-bottom: 8px; padding-left: 24px; }
  .contact-item {
    display: flex;
    align-items: center;
    gap: 8px;
  }
  .contact-item svg { width: 14px; height: 14px; flex: none; }
</style>
</head>
<body>
<main class="canvas">

  <section class="card card-front" aria-label="Card front">
    <h1 class="brand-name">
      <span class="line-main">Harborline</span>
      <span class="line-sub">Holdings</span>
    </h1>
    <p class="front-web">www.harborline.com</p>
  </section>

  <section class="card card-back" aria-label="Card back">
    <div class="name-block">
      <p class="person-name">Daniel Mercer</p>
      <p class="person-title">Director</p>
    </div>
    <div class="contact-panel">
      <span class="panel-rule"></span>
      <ul class="contact-list">
        <li class="address">4100 Cedar Lane<br>Marlow TX 78000</li>
        <li class="contact-item">
          <svg viewBox="0 0 16 16" aria-hidden="true"><path fill="#fff" d="M3.5 1.5l2.5 0 1 3.5-1.6 1.2a9 9 0 0 0 4.4 4.4L11 9l3.5 1v2.5c0 1-1 2-2 2A11 11 0 0 1 1.5 3.5c0-1 1-2 2-2z"/></svg>
          <span>512 004 2200</span>
        </li>
        <li class="contact-item">
          <svg viewBox="0 0 16 16" aria-hidden="true"><path fill="#fff" d="M4 1h8v4H4zM1 6h14v6h-3v3H4v-3H1zM5 10v4h6v-4z"/></svg>
          <span>512 004 2201</span>
        </li>
        <li class="contact-item">
          <svg viewBox="0 0 16 16" aria-hidden="true"><path fill="#fff" d="M1 3h14v10H1zM2 4.2v.4l6 4.2 6-4.2v-.4z"/></svg>
          <span>info@harborline.com</span>
        </li>
        <li class="contact-item">
          <svg viewBox="0 0 16 16" aria-hidden="true"><g fill="none" stroke="#fff" stroke-width="1.4"><circle cx="8" cy="8" r="6.3"/><ellipse cx="8" cy="8" rx="2.8" ry="6.3"/><path d="M1.7 8h12.6M2.8 4.8h10.4M2.8 11.2h10.4"/></g></svg>
          <span>www.harborline.com</span>
        </li>
      </ul>
    </div>
  </section>

</main>
</body>
</html>
```